Business Card Design Project

I am opening a skin care studio called Glow Haven by Marisol. I will be offering a wide range of unique and affordable skin services including facials, chemical peels, microdermabrasion treatments, body wraps, salt glows, all waxing and eye lash extensions. If the business cards depicts what I would like, this would lead to brochures, web design, signs, etc.

Project Deadline Extended
Reason: A request to extend deadline was requested. I will be more than happy to accommodate.

Industry/Entity Type

Business

Requirements
Nice to have
• facial features so prospective client clearly identifies what type of business this is. Not stuffy or boring "spa" looking graphics. I am focusing just on face, body, waxing, eyelashes. No massage or nails.

```html
<!DOCTYPE html>
<html lang="en">
<head>
<meta charset="utf-8">
<title>Glow Haven by Marisol — Business Card</title>
<link rel="stylesheet" href="https://fonts.googleapis.com/css2?family=Questrial&family=Roboto+Condensed:wght@400&display=swap">
<style>
  :root {
    --page-bg: #f2f2f2;
    --card-dark: #161616;
    --card-mid: #2a2a2a;
    --ink-light: #ffffff;
    --ink-soft: #e8e8e8;
  }
  * { margin: 0; padding: 0; box-sizing: border-box; }
  html, body {
    width: 1200px;
    height: 1200px;
    overflow: hidden;
    background: var(--page-bg);
  }
  .sheet {
    width: 1200px;
    height: 1200px;
    display: flex;
    flex-direction: column;
    align-items: center;
    justify-content: center;
    gap: 60px;
  }
  .card {
    position: relative;
    width: 880px;
    height: 503px;
    background: linear-gradient(135deg, var(--card-dark) 0%, var(--card-mid) 100%);
    color: var(--ink-light);
    box-shadow: 0 6px 18px rgba(0,0,0,0.18);
  }
  /* Front */
  .card-front {
    display: flex;
    flex-direction: column;
    align-items: center;
    justify-content: center;
    text-align: center;
  }
  .brand-name {
    font-family: "Questrial", sans-serif;
    font-size: 74px;
    font-weight: 400;
    letter-spacing: 3px;
    line-height: 1;
  }
  .brand-tagline {
    font-family: "Questrial", sans-serif;
    font-size: 30px;
    letter-spacing: 1px;
    margin-top: 14px;
  }
  /* Back */
  .appointment {
    position: absolute;
    left: 64px;
    top: 62px;
    font-family: "Roboto Condensed", sans-serif;
    color: var(--ink-soft);
  }
  .appointment-title {
    font-size: 40px;
    letter-spacing: 0.5px;
    margin-bottom: 18px;
  }
  .appointment-field {
    font-size: 38px;
    margin-left: 6px;
    margin-bottom: 12px;
    white-space: pre;
  }
  .contact {
    position: absolute;
    right: 40px;
    bottom: 42px;
    text-align: right;
    font-family: "Questrial", sans-serif;
    font-size: 25px;
    line-height: 1.35;
    color: var(--ink-soft);
  }
</style>
</head>
<body>
  <main class="sheet">
    <section class="card card-front" aria-label="Card front">
      <h1 class="brand-name">GLOW HAVEN</h1>
      <p class="brand-tagline">by marisol</p>
    </section>

    <section class="card card-back" aria-label="Card back">
      <div class="appointment">
        <p class="appointment-title">APPOINTMENT</p>
        <p class="appointment-field">DATE ....\....\.....</p>
        <p class="appointment-field">TIME  .....:.....</p>
      </div>
      <address class="contact" style="font-style: normal;">
        <p>418 Alder Street Fairview, CO 80999</p>
        <p>555-014-2290</p>
        <p>glowhavenbymarisol.com</p>
      </address>
    </section>
  </main>
</body>
</html>
```